Calvanto Group Real Estate Company business cards

New business card design, we are generally happy with the basic layout of the existing front of business card, (feel free to change) but require a head shot photo on the back side.

http://www.calvanto.com.au/

Attached logos, and existing business card

------------------------------

Target Market(s)

Real estate

Industry/Entity Type

Real Estate

Contact Information for Business Card

Standard size double sided

Font styles to use
Other font styles liked:
• Futura

Requirements
Must have
• Photo head shot on the back side
Nice to have
• yes
Should not have
• No

```html
<!DOCTYPE html>
<html lang="en">
<head>
<meta charset="utf-8">
<title>Calvanto Group business cards</title>
<link rel="stylesheet" href="https://fonts.googleapis.com/css2?family=Open+Sans:wght@400;600;700&display=swap">
<style>
  :root {
    --backdrop: #3a3a3c;
    --card: #1a1a1b;
    --card-edge: #232325;
    --orange: #f39a1e;
    --white: #f2f2f2;
    --grey: #9a9a9c;
    --purple: #3b2a86;
    --photo-light: #e9ecef;
    --photo-mid: #b9c0c8;
  }
  * { box-sizing: border-box; margin: 0; padding: 0; }
  html, body { width: 1200px; height: 900px; overflow: hidden; }
  body {
    background: var(--backdrop);
    font-family: "Open Sans", sans-serif;
    position: relative;
  }
  .card {
    position: absolute;
    top: 291px;
    width: 520px;
    height: 318px;
    background: var(--card);
    border: 1px solid var(--card-edge);
    border-radius: 22px;
    overflow: hidden;
  }
  .card--profile { left: 60px; }
  .card--brand { left: 620px; }

  .profile-photo {
    position: absolute;
    left: 58px;
    top: 84px;
    width: 170px;
    height: 150px;
    border-radius: 50%;
    background: radial-gradient(circle at 50% 45%, var(--photo-light) 0%, var(--photo-mid) 70%, var(--card) 100%);
  }
  .profile-divider {
    position: absolute;
    left: 260px;
    top: 70px;
    width: 1px;
    height: 170px;
    background: #2b2b2d;
  }
  .profile-details {
    position: absolute;
    left: 282px;
    top: 62px;
    color: var(--white);
  }
  .person-name { color: var(--orange); font-weight: 700; font-size: 17px; line-height: 1.2; }
  .person-role { font-size: 11px; margin-bottom: 10px; }
  .company-name { color: var(--orange); font-weight: 700; font-size: 15px; line-height: 1.2; }
  .company-abn { font-size: 12px; margin-bottom: 22px; }
  .company-abn b { font-weight: 700; }
  .contact-list { list-style: none; font-size: 12.5px; }
  .contact-list li { display: flex; align-items: center; gap: 10px; height: 22px; }
  .contact-list svg { width: 11px; height: 11px; fill: var(--orange); flex: none; }

  .brand-block {
    position: absolute;
    inset: 0;
    display: flex;
    flex-direction: column;
    align-items: center;
    justify-content: center;
  }
  .brand-name {
    color: var(--purple);
    font-weight: 600;
    font-size: 58px;
    letter-spacing: -1px;
    line-height: 1;
  }
  .brand-tagline { color: var(--grey); font-weight: 600; font-size: 13px; margin-top: 10px; }
  .brand-services { color: var(--orange); font-weight: 700; font-size: 15px; margin-top: 8px; }
</style>
</head>
<body>
  <section class="card card--profile">
    <div class="profile-photo" role="img" aria-label="Head shot photo of the director"></div>
    <div class="profile-divider"></div>
    <div class="profile-details">
      <p class="person-name">Daniel Tran</p>
      <p class="person-role">Director</p>
      <p class="company-name">Calvanto Group</p>
      <p class="company-abn"><b>ABN:</b> 12 345 678 901</p>
      <ul class="contact-list">
        <li>
          <svg viewBox="0 0 24 24" aria-hidden="true"><path d="M6.6 10.8a15.1 15.1 0 0 0 6.6 6.6l2.2-2.2c.3-.3.7-.4 1-.2 1.1.4 2.3.6 3.6.6.6 0 1 .4 1 1V20c0 .6-.4 1-1 1A17 17 0 0 1 3 4c0-.6.4-1 1-1h3.5c.6 0 1 .4 1 1 0 1.3.2 2.5.6 3.6.1.3 0 .7-.2 1z"/></svg>
          <span>0400 555 218</span>
        </li>
        <li>
          <svg viewBox="0 0 24 24" aria-hidden="true"><path d="M2 5h20v14H2z M2 5l10 8 10-8" stroke="#1a1a1b" stroke-width="1.5"/></svg>
          <span>daniel.tran@calvanto.com.au</span>
        </li>
        <li>
          <svg viewBox="0 0 24 24" aria-hidden="true"><circle cx="12" cy="12" r="10"/></svg>
          <span>www.calvanto.com.au</span>
        </li>
      </ul>
    </div>
  </section>

  <section class="card card--brand">
    <div class="brand-block">
      <p class="brand-name">calvanto</p>
      <p class="brand-tagline">let us show you property</p>
      <p class="brand-services">Buy - Sell - Rent</p>
    </div>
  </section>
</body>
</html>
```